Mara Penrith Copywriter Website

I am starting a new business as a freelance copywriter. Trying to set up the website for my business is proving to be too technical for me. I would like a simple, clean website using primarily black and white. I have attached the logo I would like used. I would like the menu icons to be Home, Services, Portfolio, Blog, Contact. I would like my mobile phone number (0412 583 906) and email address (mara.penrith.copywriter@fernmail.test) used in the header of the site. I need the site to be easily manageable and inter-changeable for me to be able to move things around and add images, etc with ease.

I would like the home page to be a static page with space for an image of myself somewhere (I haven't had this taken as yet), an area to put a bit about myself and my business, and also somewhere to include social media icons/links. Again, I would like the whole website and home page to be easily managed so that I can add/delete things with ease.

I would like the image of the typewriter used in the website somewhere also please.

Coding

Coded - Design and coding required

Number of Pages Required

5+ page

Font styles to use
Sans Serif
Script

Colors
fdf0f6

Requirements
Must have
• The logo provided
• Ability to change page contents easily
• Ability to add social media icons as needed
Nice to have
• Use of the typewriter image
Should not have
• Complicated pages that are not easily editable

```html
<!DOCTYPE html>
<html lang="en">
<head>
<meta charset="utf-8">
<title>Mara Penrith Copywriter</title>
<link rel="stylesheet" href="https://fonts.googleapis.com/css2?family=Parisienne&family=Montserrat:wght@400;500;600;700&family=Open+Sans:wght@400;600&display=swap">
<style>
  :root {
    --ink: #111111;
    --text: #444444;
    --muted: #777777;
    --line: #dddddd;
    --paper: #ffffff;
    --band: #f2f2f2;
    --blush: #fdf0f6;
    --blush-deep: #f6dfe6;
    --hero-dark: #3a3a3a;
    --hero-mid: #6b6b6b;
  }
  * { box-sizing: border-box; margin: 0; padding: 0; }
  html, body { width: 1200px; height: 3564px; overflow: hidden; }
  body { position: relative; background: var(--paper); color: var(--text); font-family: "Open Sans", Arial, sans-serif; }
  .abs { position: absolute; }
  .script { font-family: "Parisienne", cursive; color: var(--ink); font-weight: 400; }
  .section-title { position: absolute; left: 0; width: 1200px; text-align: center; font-size: 44px; }

  /* top bar */
  .topbar { left: 76px; top: 0; width: 1048px; height: 52px; border-bottom: 1px solid var(--line); }
  .social { position: absolute; left: 0; top: 17px; display: flex; gap: 12px; }
  .social span { width: 16px; height: 16px; border-radius: 50%; background: var(--ink); display: block; }
  .contact { position: absolute; right: 0; top: 16px; display: flex; gap: 28px; font-size: 14px; color: var(--text); align-items: center; }
  .contact div { display: flex; gap: 10px; align-items: center; }

  /* header */
  .header { left: 0; top: 52px; width: 1200px; height: 110px; background: linear-gradient(90deg, #ffffff 0%, #f4f4fa 60%, #eceef8 100%); }
  .logo { position: absolute; left: 76px; top: 34px; width: 330px; height: 50px; background: var(--blush-deep); border-radius: 25px; display: flex; align-items: center; justify-content: center; font-family: "Montserrat", sans-serif; font-size: 22px; font-weight: 500; color: var(--ink); }
  .nav { position: absolute; right: 76px; top: 44px; display: flex; gap: 46px; font-family: "Montserrat", sans-serif; font-size: 15px; color: #555; letter-spacing: .5px; }
  .nav .active { color: var(--ink); font-weight: 600; }

  /* hero */
  .hero { left: 0; top: 162px; width: 1200px; height: 532px; background: linear-gradient(100deg, var(--hero-dark) 0%, var(--hero-mid) 55%, #8a8a8a 100%); }
  .hero-title { position: absolute; left: 78px; top: 120px; font-size: 64px; color: #fff; }
  .hero-text { position: absolute; left: 78px; top: 210px; width: 440px; font-size: 18px; line-height: 30px; color: #fff; }
  .btn { position: absolute; height: 48px; border-radius: 24px; display: flex; align-items: center; justify-content: center; font-family: "Montserrat", sans-serif; font-weight: 700; font-size: 17px; }
  .btn-light { background: #fff; color: var(--ink); }
  .btn-dark { background: var(--ink); color: #fff; }

  /* newsletter */
  .subscribe { left: 298px; top: 840px; width: 604px; height: 50px; border-radius: 25px; background: #fff; box-shadow: 0 2px 10px rgba(0,0,0,.1); }
  .subscribe span { position: absolute; left: 38px; top: 15px; font-size: 15px; color: #666; }
  .subscribe .btn { right: 0; top: 0; width: 168px; height: 50px; border-radius: 25px; font-size: 19px; }

  /* about */
  .about-frame { left: 202px; top: 967px; width: 290px; height: 311px; background: var(--blush); }
  .about-photo { left: 76px; top: 986px; width: 394px; height: 416px; background: linear-gradient(160deg, #b9b2a6, #d8cfc2 50%, #a59a8a); }
  .about-title { position: absolute; left: 580px; top: 1012px; font-size: 44px; }
  .about-text { position: absolute; left: 576px; top: 1078px; width: 526px; font-size: 15px; line-height: 28px; color: var(--text); }

  /* services */
  .services-band { left: 0; top: 1490px; width: 1200px; height: 487px; background: var(--band); }
  .services-card { left: 76px; top: 1608px; width: 1045px; height: 293px; background: #fff; box-shadow: 0 2px 8px rgba(0,0,0,.08); display: flex; }
  .service { flex: 1; text-align: center; padding-top: 54px; border-right: 1px solid var(--line); margin: 40px 0 50px; padding-top: 14px; }
  .service:last-child { border-right: none; }
  .service h3 { font-family: "Montserrat", sans-serif; font-size: 20px; font-weight: 500; color: #333; margin-top: 18px; }
  .service hr { width: 36px; border: none; border-top: 3px solid var(--ink); margin: 14px auto 18px; }
  .service p { font-size: 14px; line-height: 26px; color: var(--text); }
  .service a { display: inline-block; margin-top: 8px; font-size: 14px; color: #444; text-decoration: underline; }

  /* portfolio */
  .project { position: absolute; }
  .project-label { position: absolute; font-size: 17px; color: #555; }

  /* blog */
  .blog-band { left: 0; top: 2875px; width: 1200px; height: 625px; background: var(--band); }
  .blog-photo { left: 76px; top: 2998px; width: 523px; height: 385px; background: linear-gradient(135deg, #4b3a30, #8a6d57 45%, #d5cfc9); }
  .blog-card { left: 599px; top: 2998px; width: 522px; height: 385px; background: #fff; padding: 72px 60px 0 62px; }
  .blog-card h4 { font-family: "Montserrat", sans-serif; font-size: 18px; font-weight: 600; line-height: 32px; color: #222; }
  .blog-card hr { width: 40px; border: none; border-top: 3px solid var(--ink); margin: 18px 0 16px; }
  .blog-date { display: flex; align-items: center; gap: 12px; font-size: 15px; color: #333; }
  .blog-card p { margin-top: 18px; font-size: 14px; line-height: 28px; color: var(--text); }
  .dots { left: 555px; top: 3418px; display: flex; gap: 8px; }
  .dots span { width: 16px; height: 16px; border-radius: 50%; border: 2px solid var(--ink); display: block; }
  .dots .on { background: var(--ink); }

  .footer { left: 0; top: 3500px; width: 1200px; height: 64px; text-align: center; line-height: 64px; font-size: 14px; color: #555; }
</style>
</head>
<body>

<!-- top bar -->
<div class="abs topbar">
  <div class="social" aria-label="Social links"><span></span><span></span><span></span><span></span></div>
  <div class="contact">
    <div>
      <svg width="18" height="13" viewBox="0 0 18 13"><rect x="0.5" y="0.5" width="17" height="12" fill="#111"/><path d="M1 1l8 6 8-6" stroke="#fff" fill="none" stroke-width="1.3"/></svg>
      mara.penrith.copywriter@fernmail.test
    </div>
    <div>
      <svg width="16" height="16" viewBox="0 0 24 24"><path d="M6.6 10.8a15 15 0 0 0 6.6 6.6l2.2-2.2a1 1 0 0 1 1-.25 11.4 11.4 0 0 0 3.6.57 1 1 0 0 1 1 1V20a1 1 0 0 1-1 1A17 17 0 0 1 3 4a1 1 0 0 1 1-1h3.5a1 1 0 0 1 1 1c0 1.25.2 2.45.57 3.57a1 1 0 0 1-.25 1z" fill="#111"/></svg>
      (0412 583 906)
    </div>
  </div>
</div>

<!-- header -->
<header class="abs header">
  <div class="logo">Mara Penrith Copywriter</div>
  <nav class="nav">
    <span class="active">HOME</span><span>SERVICES</span><span>PORTFOLIO</span><span>BLOG</span><span>CONTACT</span>
  </nav>
</header>

<!-- hero -->
<section class="abs hero" role="img" aria-label="Photo of a white vintage typewriter beside a notebook and tablet on a dark wooden desk">
  <h1 class="script hero-title">mara penrith</h1>
  <p class="hero-text">Lorem Ipsum is simply dummy text of the printing and typesetting industry. Lorem Ipsum has been the industry's standard dummy text ever.</p>
  <div class="btn btn-light" style="left:78px;top:326px;width:186px;">KNOW MORE</div>
  <div class="btn btn-light" style="left:285px;top:326px;width:188px;">CONTACT ME</div>
</section>

<!-- newsletter -->
<h2 class="script section-title" style="top:750px;">Subscribe to my Newsletter</h2>
<div class="abs subscribe">
  <span>Enter your email</span>
  <div class="btn btn-dark">SUBMIT</div>
</div>

<!-- about -->
<div class="abs about-frame"></div>
<div class="abs about-photo" role="img" aria-label="Portrait photo of the copywriter outdoors in a white summer top"></div>
<h2 class="script about-title">About mara penrith</h2>
<p class="about-text">It was popularised in the 1960s with the release of sheets containing passages, and more recently with desktop publishing software. An unknown printer took a galley of type and scrambled it to make a type specimen book. It has survived not only five centuries, but also the leap into electronic typesetting, remaining essentially unchanged.</p>
<div class="btn btn-dark" style="left:575px;top:1316px;width:186px;">KNOW MORE</div>

<!-- services -->
<div class="abs services-band"></div>
<h2 class="script section-title" style="top:1530px;">Services</h2>
<div class="abs services-card">
  <div class="service">
    <svg width="36" height="30" viewBox="0 0 36 30" fill="none" stroke="#111" stroke-width="1.6"><rect x="1" y="1" width="34" height="22"/><path d="M1 6h34M12 29h12M18 23v6"/><path d="M14 15l4-4 4 4"/></svg>
    <h3>Landing Pages</h3><hr>
    <p>Lorem Ipsum is simply dummy<br>text of the printing and typeset.</p>
    <a>READ MORE</a>
  </div>
  <div class="service">
    <svg width="36" height="30" viewBox="0 0 36 30" fill="none" stroke="#111" stroke-width="1.6"><rect x="1" y="9" width="34" height="20"/><path d="M1 9l17 12 17-12M8 12V1h20v11M12 6h12"/></svg>
    <h3>Online sales letter</h3><hr>
    <p>Lorem Ipsum is simply dummy<br>text of the printing and typeset.</p>
    <a>READ MORE</a>
  </div>
  <div class="service">
    <svg width="28" height="34" viewBox="0 0 28 34" fill="none" stroke="#111" stroke-width="1.6"><rect x="1" y="1" width="26" height="32"/><path d="M6 8h16M6 14h16M6 20h16M6 26h10"/></svg>
    <h3>Promotional emails</h3><hr>
    <p>Lorem Ipsum is simply dummy<br>text of the printing and typeset.</p>
    <a>READ MORE</a>
  </div>
  <div class="service">
    <svg width="36" height="30" viewBox="0 0 36 30" fill="none" stroke="#111" stroke-width="1.6"><path d="M1 12l17-11 17 11v17H1z"/><path d="M1 12l17 11 17-11"/><rect x="9" y="6" width="18" height="10"/></svg>
    <h3>Email marketing</h3><hr>
    <p>Lorem Ipsum is simply dummy<br>text of the printing and typeset.</p>
    <a>READ MORE</a>
  </div>
</div>

<!-- portfolio -->
<h2 class="script section-title" style="top:2018px;">Work Portfolio</h2>
<div class="project" style="left:78px;top:2098px;width:333px;height:249px;background:linear-gradient(135deg,#6b5a4a,#b8a48c);" role="img" aria-label="Project photo: woman working at a laptop in a cafe"></div>
<div class="project-label" style="left:80px;top:2368px;">Project Name</div>
<div class="project" style="left:78px;top:2414px;width:333px;height:342px;background:linear-gradient(180deg,#c9c4b4,#a89f8a 60%,#6d6f7a);" role="img" aria-label="Project photo: children playing outdoors on a skateboard"></div>
<div class="project-label" style="left:80px;top:2776px;">Project Name</div>

<div class="project" style="left:432px;top:2098px;width:333px;height:345px;background:linear-gradient(180deg,#7c7c7c,#cfc7b6 50%,#e6e3de);" role="img" aria-label="Project photo: person holding a straw hat"></div>
<div class="project-label" style="left:436px;top:2463px;">Project Name</div>
<div class="project" style="left:432px;top:2507px;width:333px;height:249px;background:linear-gradient(135deg,#8d9aa6,#d9d4cf 60%,#c45a5a);" role="img" aria-label="Project photo: woman with a toothbrush"></div>
<div class="project-label" style="left:436px;top:2776px;">Project Name</div>

<div class="project" style="left:789px;top:2098px;width:333px;height:249px;background:linear-gradient(180deg,#9ccbe0,#e9b9c4 60%,#d28a7a);" role="img" aria-label="Project photo: dog in sunglasses on a beach boat"></div>
<div class="project-label" style="left:792px;top:2368px;">Project Name</div>
<div class="project" style="left:789px;top:2414px;width:333px;height:342px;background:linear-gradient(180deg,#d8d2c6,#b3a894 60%,#8f8a84);" role="img" aria-label="Project photo: traveller with a suitcase on a narrow street"></div>
<div class="project-label" style="left:792px;top:2776px;">Project Name</div>

<!-- blog -->
<div class="abs blog-band"></div>
<h2 class="script section-title" style="top:2914px;">Latest Blog</h2>
<div class="abs blog-photo" role="img" aria-label="Overhead photo of hands typing on a laptop next to a coffee cup"></div>
<article class="abs blog-card">
  <h4>Lorem Ipsum is simply dummy text of the printing and typesetting industry Lorem Ipsum is simply.</h4>
  <hr>
  <div class="blog-date">
    <svg width="18" height="18" viewBox="0 0 18 18" fill="none" stroke="#111" stroke-width="1.6"><rect x="1" y="3" width="16" height="14"/><path d="M1 7h16M5 1v4M13 1v4"/></svg>
    24 JUL 2018
  </div>
  <p>Lorem Ipsum is simply dummy text of the printing and typesetting industry. Lorem Ipsum has been the industry's standard dummy text ever since the 1500s, when an unknown printer took a galley of type and scrambled it to make a type specimen book.</p>
</article>
<div class="abs dots"><span></span><span></span><span></span><span class="on"></span></div>

<footer class="abs footer">2018 ©mara penrith- All Rights Reserved.</footer>

</body>
</html>
```